Psychiatric Office Needs a Website- 1st Time Ever!

Been in practice since 2003 with no website, but finally ready to dive in. We are Maplecrest Behavioral Healthcare, a mental health outpatient practice based in Fayetteville, Georgia that sees diverse individuals and families from childhood to advanced age for a variety of conditions. We've grown by word of mouth and referral but would now like to have a digital footprint. Be the pioneer of our website and we will be sure to share. We would like to see designs that are modern, animated, fairly colorful, easy to read, and caters to all ages. Also, we would like the design to take the whole page (not be centered) and can be viewed well on phone/tablet. Please see our outline for more information. Our motto/slogan is: Maplecrest Behavioral Healthcare- A step forward in your wellness journey, so the design should try to reflect that.
Updates

Project Deadline Extended
Reason: site in progress

Target Market(s)

Children through elderly

Industry/Entity Type

Medical

Logo Text

Stepping forward in your wellness journey

Number of Pages Required

1 page

Colors

Designer to choose colors to be used in the design.

Requirements
Must have
• Animation or moving pictures.
• Color.
• Concise.
• User friendly
• Diversity in the stock photos

```html
<!DOCTYPE html>
<html lang="en">
<head>
<meta charset="utf-8">
<title>Maplecrest Behavioral Healthcare</title>
<link href="https://fonts.googleapis.com/css2?family=Ubuntu:wght@400;500;700&family=Open+Sans:wght@400;600;700&display=swap" rel="stylesheet">
<style>
:root{
  --navy:#0d3d6e;
  --accent:#1d8fd1;
  --ink:#1e1e1e;
  --text:#555;
  --muted:#777;
  --band:#f3f3f3;
  --white:#fff;
  --line:#e2e2e2;
}
*{box-sizing:border-box;margin:0;padding:0}
html,body{width:1200px;height:3103px;overflow:hidden}
body{font-family:"Open Sans",Arial,sans-serif;color:var(--text);background:var(--white);position:relative}
.btn{position:absolute;background:var(--navy);color:var(--white);font:700 11px "Open Sans",sans-serif;letter-spacing:.4px;text-transform:uppercase;border-radius:20px;display:flex;align-items:center;justify-content:center}
.section-title{position:absolute;left:0;width:1200px;text-align:center;font:700 29px "Ubuntu",sans-serif;color:var(--ink);letter-spacing:.3px}

/* hero */
.hero{position:absolute;left:0;top:0;width:1200px;height:498px;overflow:hidden}
.hero-photo{position:absolute;inset:0;background:linear-gradient(100deg,#c9e0f3 0%,#9cc6ea 30%,#b8d7f0 55%,#e4eef6 78%,#cfd8df 100%)}
.brand{position:absolute;left:186px;top:14px;display:flex;align-items:center;gap:8px}
.brand-dot{width:20px;height:20px;border-radius:50%;background:var(--navy)}
.brand-name{font:700 15px "Ubuntu",sans-serif;color:var(--navy);line-height:1.1;width:140px}
.topbar{position:absolute;top:17px;left:588px;display:flex;align-items:center;gap:22px;font:600 11px "Open Sans",sans-serif;color:var(--ink)}
.topbar span{display:flex;align-items:center;gap:5px}
.portal{background:var(--white);color:var(--navy);padding:5px 20px;border-radius:14px;font-weight:700;margin-left:-4px}
.nav{position:absolute;top:53px;left:555px;display:flex;gap:6px;font:700 10.5px "Open Sans",sans-serif;color:var(--navy);text-transform:uppercase}
.nav a{padding:6px 10px;border-radius:14px;color:inherit;text-decoration:none}
.nav a.active{background:var(--navy);color:var(--white)}
.hero-title{position:absolute;top:224px;left:0;width:1200px;text-align:center;font:700 30px "Ubuntu",sans-serif;color:var(--navy);letter-spacing:.5px}
.hero-sub{position:absolute;top:266px;left:0;width:1200px;text-align:center;font:400 19px "Ubuntu",sans-serif;color:var(--ink)}
.dots{position:absolute;top:446px;left:554px;display:flex;gap:20px}
.dots i{width:10px;height:10px;border-radius:50%;background:var(--navy);opacity:.75}

/* vision */
.vm-col{position:absolute;top:655px;width:390px}
.vm-label{display:flex;align-items:center;gap:14px;font:700 18px "Ubuntu",sans-serif;color:var(--navy)}
.vm-text{margin-top:38px;font-size:13px;line-height:24px;color:var(--muted)}

/* services */
.services{position:absolute;top:900px;left:0;width:1200px;height:895px;background:var(--band)}
.svc-list{position:absolute;left:155px;top:155px;list-style:none}
.svc-list li{position:relative;padding-left:26px;font:400 18px "Ubuntu",sans-serif;color:var(--ink);line-height:23px}
.svc-list li::before{content:"";position:absolute;left:0;top:8px;width:8px;height:8px;border-radius:50%;border:2px solid var(--ink)}
.svc-list li.active{color:var(--accent)}
.svc-list li.active::before{border-color:var(--accent);background:var(--accent)}
.svc-list small{display:block;font:400 11px "Open Sans",sans-serif}
.svc-photo{position:absolute;left:393px;top:158px;width:631px;height:330px;background:linear-gradient(135deg,#d6dadf,#a9b6c3 45%,#f1c6b6 70%,#5f6d80)}
.svc-head{position:absolute;left:391px;top:532px;font:400 24px "Ubuntu",sans-serif;color:var(--accent)}
.svc-body{position:absolute;left:391px;top:580px;width:635px;font-size:10.4px;line-height:24px;color:var(--text)}

/* conditions */
.cond-card{position:absolute;top:1936px;width:198px}
.cond-photo{height:124px}
.cond-title{margin-top:22px;font:700 15px "Ubuntu",sans-serif;color:var(--navy);line-height:20px}
.cond-list{list-style:none;margin-top:34px;font-size:11.5px;color:var(--text)}
.cond-list li{position:relative;padding-left:18px;line-height:24px}
.cond-list li::before{content:"›";position:absolute;left:0;color:var(--accent);font-weight:700;font-size:15px}

/* faqs */
.faqs{position:absolute;top:2330px;left:0;width:1200px;height:485px;background:var(--band)}
.faq{position:absolute;width:440px}
.faq h3{font:700 14px "Ubuntu",sans-serif;color:var(--ink);white-space:nowrap}
.faq p{margin-top:16px;font-size:11px;line-height:22px;color:var(--text)}

/* footer */
.footer-col{position:absolute;top:2858px}
.footer-col h4{font:700 10px "Open Sans",sans-serif;color:var(--navy);text-transform:uppercase;margin-bottom:26px}
.footer-col li{list-style:none;font-size:10.5px;line-height:19px;color:var(--ink)}
.contact{width:165px}
.contact-row{display:flex;gap:12px;align-items:flex-start;font-size:10px;line-height:17px;color:var(--ink);margin-bottom:20px;white-space:nowrap}
.contact-row svg{flex:none;margin-top:3px}
.map{position:absolute;left:805px;top:2855px;width:228px;height:150px;background:linear-gradient(135deg,#e8e8e8,#d2d4d6)}
.bottombar{position:absolute;top:3020px;left:0;width:1200px;height:83px;border-top:1px solid var(--line);background:var(--white)}
.foot-brand{position:absolute;left:172px;top:34px;display:flex;align-items:center;gap:8px;font:700 24px "Ubuntu",sans-serif;color:var(--navy)}
.foot-brand i{width:20px;height:20px;border-radius:50%;background:var(--navy)}
.social{position:absolute;left:324px;top:42px;font:700 10.5px "Open Sans",sans-serif;color:var(--navy);text-transform:uppercase}
.copy{position:absolute;right:170px;top:42px;font-size:10.5px;color:var(--ink)}
</style>
</head>
<body>

<header class="hero">
  <div class="hero-photo" role="img" aria-label="Soft blurred clinic corridor with a doctor holding a stethoscope on the right"></div>
  <div class="brand"><span class="brand-dot"></span><span class="brand-name">Maplecrest Behavioral Healthcare</span></div>
  <div class="topbar">
    <span><svg width="11" height="11" viewBox="0 0 24 24"><path fill="#1e1e1e" d="M6.6 10.8a15 15 0 006.6 6.6l2.2-2.2c.3-.3.7-.4 1-.2 1.1.4 2.3.6 3.6.6.6 0 1 .4 1 1V20c0 .6-.4 1-1 1A17 17 0 013 4c0-.6.4-1 1-1h3.5c.6 0 1 .4 1 1 0 1.3.2 2.5.6 3.6.1.3 0 .7-.2 1z"/></svg>1-800-555-0148</span>
    <span><svg width="11" height="11" viewBox="0 0 24 24"><circle cx="12" cy="12" r="9" fill="none" stroke="#1e1e1e" stroke-width="2.5"/><path d="M12 7v5l3 2" stroke="#1e1e1e" stroke-width="2.5" fill="none"/></svg>Mon -Fri &nbsp; 8:00 AM to 5PM &nbsp;&nbsp; Sat -Sun - Holiday</span>
    <span class="portal">PATIENT PORTAL</span>
  </div>
  <nav class="nav">
    <a class="active">Home</a><a>About Us</a><a>Services</a><a>Conditions We Treat</a><a>New Patients</a><a>Contact Us</a>
  </nav>
  <h1 class="hero-title">MAPLECREST BEHAVIORAL HEALTHCARE</h1>
  <p class="hero-sub">A step forward in your wellness journey</p>
  <div class="btn" style="left:493px;top:312px;width:214px;height:37px">Take a Screening</div>
  <div class="dots"><i></i><i></i><i></i><i></i></div>
</header>

<section>
  <h2 class="section-title" style="top:557px">VISION &amp; MISSION</h2>
  <div class="vm-col" style="left:172px">
    <div class="vm-label"><svg width="30" height="18" viewBox="0 0 30 18"><path d="M1 9C6 2 11 1 15 1s9 1 14 8c-5 7-10 8-14 8S6 16 1 9z" fill="var(--accent)"/><circle cx="15" cy="9" r="5" fill="#fff"/><circle cx="15" cy="9" r="3" fill="var(--accent)"/></svg>Vision</div>
    <p class="vm-text">To be the leading provider of outpatient psychiatric care in Atlanta Metro South, working together to promote (the) mental wellness of our community.</p>
  </div>
  <div class="btn" style="left:172px;top:824px;width:106px;height:33px">Read More</div>
  <div class="vm-col" style="left:610px">
    <div class="vm-label"><svg width="30" height="24" viewBox="0 0 30 24"><rect x="2" y="6" width="11" height="17" rx="4" fill="var(--accent)"/><rect x="17" y="6" width="11" height="17" rx="4" fill="var(--accent)"/><rect x="4" y="1" width="7" height="7" rx="2" fill="var(--accent)"/><rect x="19" y="1" width="7" height="7" rx="2" fill="var(--accent)"/><rect x="12" y="9" width="6" height="6" fill="var(--accent)"/></svg>Mission</div>
    <p class="vm-text">To provide mental health services to children, adults,and the developmentally disabled population that is culturally sensitive regardless of age, race, gender, orientation, religion, or creed</p>
  </div>
  <div class="btn" style="left:610px;top:824px;width:106px;height:33px">Read More</div>
</section>

<section class="services">
  <h2 class="section-title" style="top:65px">SERVICES</h2>
  <ul class="svc-list">
    <li class="active" style="margin-bottom:33px">Diagnostic evaluation<br>and treatment</li>
    <li style="margin-bottom:37px">Psychopharmacology</li>
    <li style="margin-bottom:29px">Bariatric pre-surgical<br>consultation<small>(and other surgeries)</small></li>
    <li style="margin-bottom:29px">Disability and<br>work-related reports<small>(include?)</small></li>
    <li style="margin-bottom:37px">Early childhood<br>Assessments</li>
    <li style="margin-bottom:37px">Substance abuse<br>assessments</li>
    <li>Developmental<br>disabilities</li>
  </ul>
  <div class="svc-photo" role="img" aria-label="Clinician performing an ultrasound examination on a young patient"></div>
  <h3 class="svc-head">Diagnostic evaluation and treatment</h3>
  <p class="svc-body">At vero eos et accusamus et iusto odio dignissimos ducimus qui blanditiis praesentium voluptatum deleniti atque corrupti quos dolores et quas molestias excepturi sint occaecati cupiditate non provident, similique sunt in culpa qui officia deserunt mollitia animi, id est laborum et dolorum fuga. Et harum quidem rerum facilis est et expedita distinctio. Nam libero tempore, cum soluta nobis est eligendi optio cumque nihil impedit quo minus id quod maxime placeat facere possimus, omnis voluptas assumenda est, omnis dolor repellendus. Temporibus autem quibusdam et aut officiis debitis aut rerum necessitatibus saepe eveniet ut et voluptates repudiandae sint et molestiae non recusandae.</p>
  <div class="btn" style="left:389px;top:760px;width:144px;height:33px">Read More</div>
</section>

<section>
  <h2 class="section-title" style="top:1862px">CONDITIONS WE TREAT</h2>
  <div class="cond-card" style="left:172px">
    <div class="cond-photo" role="img" aria-label="Photo of a distressed young woman" style="background:linear-gradient(135deg,#4a3a36,#9a6a58 55%,#2b2321)"></div>
    <h3 class="cond-title">Mood Disorders</h3>
    <ul class="cond-list"><li>Depression, Bipolar</li><li>Seasonal Affective Disorder</li><li>Cyclothymic Disorder</li><li>Premenstrual Dysphoric Disorder</li><li>Disruptive Mood Dysregulation</li><li>Disorder</li></ul>
  </div>
  <div class="cond-card" style="left:392px">
    <div class="cond-photo" role="img" aria-label="Photo of an anxious woman in a pale room" style="background:linear-gradient(135deg,#b7c0c9,#7d8a98 55%,#d8dde2)"></div>
    <h3 class="cond-title">Anxiety Disorders</h3>
    <ul class="cond-list"><li>Generalized</li><li>Anxiety</li><li>Panic</li><li>PTSD</li><li>OCD</li></ul>
  </div>
  <div class="cond-card" style="left:610px">
    <div class="cond-photo" role="img" aria-label="Photo of a young child" style="background:linear-gradient(135deg,#f2e6dc,#d89a6a 50%,#b95a2c)"></div>
    <h3 class="cond-title">Common Disorders of<br>Childhood</h3>
    <ul class="cond-list" style="margin-top:14px"><li>ADHD</li><li>Oppositional Defiant Disorder</li><li>leep issues</li></ul>
  </div>
  <div class="cond-card" style="left:830px">
    <div class="cond-photo" role="img" aria-label="Photo of a person sitting alone against a wall" style="background:linear-gradient(135deg,#d9d9d9,#a3a3a3 55%,#eaeaea)"></div>
    <h3 class="cond-title">Psychotic Disorders</h3>
    <ul class="cond-list"><li>Schizophrenia</li><li>Brief Psychotic Episodes</li><li>Addiction</li><li>Eating Disorders</li></ul>
  </div>
</section>

<section class="faqs">
  <h2 class="section-title" style="top:70px">FAQS</h2>
  <div class="faq" style="left:172px;top:155px"><h3>Q. What do I need to bring with me to my first visit?</h3><p>A- Insurance card, patient forms found on our</p></div>
  <div class="faq" style="left:612px;top:155px"><h3>Q. Why is my child not doing well in school?</h3><p>A- Your child may need some testing.</p></div>
  <div class="faq" style="left:172px;top:255px"><h3>Q. How long do I have to wait to be seen?</h3><p>A- We try to have very little wait time for your convenience.</p></div>
  <div class="faq" style="left:612px;top:255px"><h3>Q. &nbsp;I feel sad, tired and I do not have energy. Is that normal?</h3><p>A- No, if you have these feeling for a long period of time, you may be suffering from depression or other mood disorders.</p></div>
  <div class="faq" style="left:172px;top:360px"><h3>Q. What typs of insurance do you accept?</h3><p>A- We accept a large variety of insurance plans.</p></div>
  <div class="faq" style="left:612px;top:360px"><h3>Q. I am have trouble with my child. Do you do therapy for children?</h3><p>A- Yes, our psychiatrist is specialized in child, and adolescent psychiatry.</p></div>
</section>

<footer>
  <div class="footer-col" style="left:176px"><h4>Quick Links</h4><ul><li>Home</li><li>About Us</li><li>Services</li><li>Conditions We Treat</li><li>New Patients</li><li>Contact Us</li></ul></div>
  <div class="footer-col" style="left:322px"><h4>Other Links</h4><ul><li>Terms Of Service</li><li>Privacy Policy</li><li>Help</li><li>Disclaimer</li></ul></div>
  <div class="footer-col" style="left:466px"><h4>Appointment Timings</h4><ul><li>Mon -Fri &nbsp;&nbsp; 8:00 AM to 5:00 PM</li><li>Sat -Sun - Holiday</li></ul></div>
  <div class="footer-col contact" style="left:628px"><h4>Contact Us</h4>
    <div class="contact-row"><svg width="9" height="12" viewBox="0 0 10 14"><path d="M5 0a5 5 0 015 5c0 4-5 9-5 9S0 9 0 5a5 5 0 015-5z" fill="var(--navy)"/><circle cx="5" cy="5" r="2" fill="#fff"/></svg><span>Maplecrest Office<br>12 Elm St | Fayetteville GA</span></div>
    <div class="contact-row"><svg width="11" height="9" viewBox="0 0 12 9"><rect width="12" height="9" rx="1" fill="var(--navy)"/><path d="M0 1l6 4 6-4" stroke="#fff" fill="none"/></svg><span>E-Mail: info@mbhc.com</span></div>
    <div class="contact-row"><svg width="10" height="10" viewBox="0 0 24 24"><path fill="var(--navy)" d="M6.6 10.8a15 15 0 006.6 6.6l2.2-2.2c.3-.3.7-.4 1-.2 1.1.4 2.3.6 3.6.6.6 0 1 .4 1 1V20c0 .6-.4 1-1 1A17 17 0 013 4c0-.6.4-1 1-1h3.5c.6 0 1 .4 1 1 0 1.3.2 2.5.6 3.6.1.3 0 .7-.2 1z"/></svg><span>1-800-555-0148</span></div>
  </div>
  <div class="map" role="img" aria-label="Street map showing the office location"></div>
  <div class="bottombar">
    <div class="foot-brand"><i></i>MBHC</div>
    <div class="social">Connect</div>
    <div class="copy">© 2017 Company Name | &nbsp;All Rights Reserved</div>
  </div>
</footer>

</body>
</html>
```